Automotive component supplier needs a business card design

We need a business card design for our company called Velran Global Components Ltd based in the UK. We are a supplier of interior and exterior components to premium car manufacturers such as Corvel Ashby, Hadley Fenn, Marquist and Tavarelli. We would like to see a modern business card design that uses the colour blue.

Target Market(s)

Premium automotive car manufacturers.

Industry/Entity Type

Automotive

Contact Information for Business Card

Company Name : Velran Global Components Limited
Address: 17 Marlow Yard, Upper Heath, Warwick, CV31 8QL, United Kingdom
Web Address : www.velrancomponents-example.co.uk

Font styles to use
Other font styles liked:
• Helvetica

Colors
3176b5
0255a3
85acd3
cfdeed
cee9f5
85cae6
34a6d7
0692cd
9bcb3c

Requirements
Must have
• Clear company logo and a mixture of blue colours.
Nice to have
• A high quality modern image.
Should not have
• Multiple colours.

```html
<!DOCTYPE html>
<html lang="en">
<head>
<meta charset="utf-8">
<title>Velran Global Components – Business Card</title>
<link rel="stylesheet" href="https://fonts.googleapis.com/css2?family=Source+Sans+3:wght@400;600;700&display=swap">
<style>
  :root {
    --stage: #e9e6e3;
    --card-white: #ffffff;
    --brand-blue: #0692cd;
    --band-blue: #0a8fcb;
    --brand-green: #9bcb3c;
    --ink: #1d1d1d;
    --on-blue: #ffffff;
  }
  * { box-sizing: border-box; margin: 0; padding: 0; }
  html, body {
    width: 1200px; height: 900px; overflow: hidden;
    background: var(--stage);
    font-family: "Source Sans 3", "Helvetica Neue", Arial, sans-serif;
  }
  .stage { position: relative; width: 1200px; height: 900px; }

  .card {
    position: absolute;
    overflow: hidden;
    box-shadow: 0 6px 18px rgba(0,0,0,0.18);
  }

  /* Front */
  .card-front {
    left: 238px; top: 62px; width: 555px; height: 343px;
    background: var(--card-white);
  }
  .card-front .band {
    position: absolute; inset: 0; width: 555px; height: 343px;
  }
  .card-front .band polygon { fill: var(--band-blue); }

  .logo-plate {
    position: absolute; left: 228px; top: 44px;
    width: 302px; height: 92px;
    background: var(--card-white);
    border-radius: 12px;
  }
  .wordmark {
    color: var(--brand-blue);
    font-weight: 700;
    text-align: center;
    line-height: 1;
  }
  .card-front .wordmark { position: absolute; left: 228px; top: 52px; width: 302px; }
  .card-front .wordmark .word-main { display: block; font-size: 54px; letter-spacing: 2px; }
  .card-front .wordmark .word-sub { display: block; font-size: 16px; letter-spacing: 1.4px; margin-top: 4px; }

  .holder { position: absolute; left: 23px; top: 124px; }
  .holder-name { color: var(--brand-blue); font-weight: 700; font-size: 19px; line-height: 1.2; }
  .holder-role { color: var(--ink); font-size: 14.5px; line-height: 1.3; }

  .contact {
    position: absolute; right: 28px; top: 184px;
    list-style: none; text-align: right;
    color: var(--on-blue); font-size: 14.5px;
  }
  .contact li { height: 20px; line-height: 20px; display: flex; justify-content: flex-end; align-items: center; gap: 6px; }
  .contact svg { width: 11px; height: 11px; fill: var(--on-blue); flex: none; }
  .contact .address { height: auto; margin-top: 8px; display: block; line-height: 21px; padding-right: 3px; }

  /* Back */
  .card-back {
    left: 457px; top: 518px; width: 560px; height: 342px;
    background: var(--brand-green);
    display: flex; align-items: center; justify-content: center;
  }
  .card-back .wordmark .word-main { display: block; font-size: 86px; letter-spacing: 3px; }
  .card-back .wordmark .word-sub { display: block; font-size: 21px; letter-spacing: 2px; margin-top: 6px; }
</style>
</head>
<body>
<main class="stage">

  <section class="card card-front" aria-label="Business card front">
    <svg class="band" viewBox="0 0 555 343" aria-hidden="true">
      <polygon points="555,0 555,343 0,343 0,228"/>
    </svg>
    <div class="logo-plate"></div>
    <div class="wordmark">
      <span class="word-main">VELRAN</span>
      <span class="word-sub">GLOBAL COMPONENTS</span>
    </div>

    <div class="holder">
      <p class="holder-name">Daniel Harwood</p>
      <p class="holder-role">Director</p>
    </div>

    <ul class="contact">
      <li>0192655014
        <svg viewBox="0 0 24 24"><path d="M6.6 10.8a15.1 15.1 0 0 0 6.6 6.6l2.2-2.2a1 1 0 0 1 1-.25 11.4 11.4 0 0 0 3.6.57 1 1 0 0 1 1 1V20a1 1 0 0 1-1 1A17 17 0 0 1 3 4a1 1 0 0 1 1-1h3.5a1 1 0 0 1 1 1c0 1.25.2 2.45.57 3.57a1 1 0 0 1-.25 1z"/></svg>
      </li>
      <li>0192655014
        <svg viewBox="0 0 24 24"><path d="M7 1h10a2 2 0 0 1 2 2v18a2 2 0 0 1-2 2H7a2 2 0 0 1-2-2V3a2 2 0 0 1 2-2zm0 3v14h10V4zm5 15.5a1.2 1.2 0 1 0 0 2.4 1.2 1.2 0 0 0 0-2.4z"/></svg>
      </li>
      <li>info@velranmail.co.uk
        <svg viewBox="0 0 24 24"><path d="M2 5h20v14H2zm2 2v.5l8 5 8-5V7zm0 2.8V17h16V9.8l-8 5z"/></svg>
      </li>
      <li>www.velrancomponents-example.co.uk
        <svg viewBox="0 0 24 24"><path d="M12 2a10 10 0 1 0 0 20 10 10 0 0 0 0-20zm-1 17.9A8 8 0 0 1 4.1 11H7c.1 3 1.3 6.1 4 8.9zM7 9H4.3A8 8 0 0 1 11 4.1C8.6 6.6 7.3 8 7 9zm6 10.9c2.7-2.8 3.9-5.9 4-8.9h2.9a8 8 0 0 1-6.9 8.9zM17 9c-.3-1-1.6-2.4-4-4.9A8 8 0 0 1 19.7 9z"/></svg>
      </li>
      <li class="address">17 Marlow Yard, Upper Heath,<br>Warwick, CV31 8QL, United Kingdom</li>
    </ul>
  </section>

  <section class="card card-back" aria-label="Business card back">
    <div class="wordmark">
      <span class="word-main">VELRAN</span>
      <span class="word-sub">GLOBAL COMPONENTS</span>
    </div>
  </section>

</main>
</body>
</html>
```